Veltrano.co - Polar Expeditions Specialists

We need a modern, visually striking business card for Veltrano.co, a company specialized in selling expedition cruises to the most remote regions on Earth, with a focus on the Arctic and Antarctica. The design should instantly communicate that the cardholder is an expert in polar travel. Use clean, premium aesthetics with cool tones like icy blue and white, possibly incorporating polar imagery (ice, glaciers, penguins, etc.)

Attached the logo

Contact Information for Business Card

Feels high-end and trustworthy.. Visually memorable — encourages people to keep it

Colors
0054AA
0677BA
7BADD7
CADEEF
E8F1F8

Requirements
Must have
• ice, glaciers, penguins, montains
Nice to have
• modern, transparente,

```html
<!DOCTYPE html>
<html lang="en">
<head>
<meta charset="UTF-8">
<title>Veltrano.co – Business Card</title>
<link href="https://fonts.googleapis.com/css2?family=Poppins:wght@600;700&family=Montserrat:wght@400;500&display=swap" rel="stylesheet">
<style>
  :root {
    --brand-blue: #2f77ba;
    --deep-blue: #0054aa;
    --ice-blue: #7badd7;
    --frost: #cadeef;
    --snow: #ffffff;
    --ink: #3a3a3a;
    --stage: #e9edf1;
  }
  * { margin: 0; padding: 0; box-sizing: border-box; }
  html, body { width: 1200px; height: 1200px; overflow: hidden; }
  body {
    background: var(--stage);
    display: flex;
    align-items: center;
    justify-content: center;
    gap: 70px;
    font-family: "Montserrat", sans-serif;
  }
  .card {
    width: 420px;
    height: 680px;
    border-radius: 34px;
    position: relative;
    overflow: hidden;
    box-shadow: 0 18px 40px rgba(0, 40, 90, 0.18);
  }

  /* Front */
  .card-front {
    background: var(--snow);
    display: flex;
    flex-direction: column;
    align-items: center;
    padding: 150px 40px 0;
    text-align: center;
  }
  .brand-name {
    font-family: "Poppins", sans-serif;
    font-weight: 700;
    font-size: 62px;
    line-height: 1;
    color: var(--brand-blue);
    letter-spacing: -0.5px;
  }
  .brand-mark {
    width: 18px; height: 18px;
    border-radius: 50%;
    background: var(--brand-blue);
    margin-bottom: 18px;
  }
  .brand-tagline {
    font-family: "Poppins", sans-serif;
    font-weight: 600;
    font-size: 19px;
    color: var(--brand-blue);
    margin-top: 8px;
  }
  .holder-name {
    font-family: "Poppins", sans-serif;
    font-weight: 700;
    font-size: 32px;
    color: var(--brand-blue);
    letter-spacing: 1px;
    margin-top: 70px;
  }
  .holder-role {
    font-size: 22px;
    color: var(--ink);
    margin-top: 2px;
  }
  .icon-row {
    display: flex;
    align-items: center;
    gap: 10px;
    width: 100%;
    margin-top: 22px;
  }
  .icon-row .rule { flex: 1; height: 2px; background: var(--brand-blue); }
  .icon {
    width: 30px; height: 30px;
    border-radius: 7px;
    background: var(--brand-blue);
    display: flex; align-items: center; justify-content: center;
  }
  .contact-list {
    list-style: none;
    font-size: 19px;
    line-height: 1.45;
    color: var(--ink);
    margin-top: 12px;
  }
  .divider { width: 100%; height: 2px; background: var(--brand-blue); margin: 14px 0 12px; }
  .address { font-size: 19px; line-height: 1.4; color: var(--ink); font-style: normal; }

  /* Back */
  .card-back { background: var(--brand-blue); }
  .back-photo {
    position: absolute; inset: 0;
    background: radial-gradient(ellipse at 45% 50%, #a9c8e6 0%, #6fa3d4 45%, #4f8bc8 100%);
  }
  .back-brand {
    position: absolute;
    left: 50%; top: 50%;
    transform: translate(-50%, -50%) rotate(-90deg);
    display: flex; flex-direction: column; align-items: flex-start;
    white-space: nowrap;
  }
  .back-brand .brand-name { color: var(--snow); font-size: 80px; }
  .back-brand .brand-tagline { color: var(--snow); font-size: 22px; margin-top: 4px; }
  .back-brand .brand-mark { background: var(--snow); margin: 0 0 14px; }
</style>
</head>
<body>
  <article class="card card-front">
    <div class="brand-mark"></div>
    <h1 class="brand-name">Veltrano.co</h1>
    <p class="brand-tagline">Polar Expeditions Specialists</p>

    <h2 class="holder-name">HENRIK DALE</h2>
    <p class="holder-role">CEO / Founder</p>

    <div class="icon-row">
      <span class="rule"></span>
      <span class="icon" aria-label="Phone">
        <svg width="18" height="18" viewBox="0 0 24 24"><path fill="#fff" d="M6.6 10.8a15 15 0 0 0 6.6 6.6l2.2-2.2c.3-.3.7-.4 1-.2 1.1.4 2.3.6 3.6.6.6 0 1 .4 1 1V20c0 .6-.4 1-1 1A17 17 0 0 1 3 4c0-.6.4-1 1-1h3.5c.6 0 1 .4 1 1 0 1.3.2 2.5.6 3.6.1.3 0 .7-.2 1z"/></svg>
      </span>
      <span class="icon" aria-label="Email">
        <svg width="18" height="18" viewBox="0 0 24 24"><path fill="#fff" d="M3 5h18v14H3z"/><path fill="none" stroke="#2f77ba" stroke-width="2" d="M3 6l9 7 9-7"/></svg>
      </span>
      <span class="icon" aria-label="Website">
        <svg width="18" height="18" viewBox="0 0 24 24"><circle cx="12" cy="12" r="9" fill="none" stroke="#fff" stroke-width="2"/><path fill="none" stroke="#fff" stroke-width="1.6" d="M3 12h18M12 3c3 3 3 15 0 18M12 3c-3 3-3 15 0 18"/></svg>
      </span>
      <span class="rule"></span>
    </div>

    <ul class="contact-list">
      <li>+43 600 12 34 567</li>
      <li>henrik.dale@Veltrano.co</li>
      <li>www.veltrano.co</li>
    </ul>
    <div class="divider"></div>
    <address class="address">P.O. Box 1290 Harbour Lane<br>Nordland AV 7310</address>
  </article>

  <article class="card card-back">
    <div class="back-photo" role="img" aria-label="Soft blue photograph of a polar bear walking on sea ice"></div>
    <div class="back-brand">
      <div class="brand-mark"></div>
      <h2 class="brand-name">Veltrano.co</h2>
      <p class="brand-tagline">Polar Expeditions Specialists</p>
    </div>
  </article>
</body>
</html>
```